Business Card for a mobile physiotherapy company

I need a layout for a business card for a mobile physiotherapy company.
Slogan is "Mobile Physiotherapy - Your Road To Recovery"
Phone number is 867-555-0142
Email VardenTherapy@postnest.ca (subject to change with website)
Website www.VardenTherapy.ca
My name and credentials: Luke Varden Luke Varden, BSc(kin), MPT, CAFCI, IMS
Information maybe included: Direct Billing, Services including Physiotherapy, IMS, acupuncture
Maybe include facebook and instagram logos
One side with the logo clean and sharp
Other side with details, try not to look too busy, keep everything concise

```html
<!DOCTYPE html>
<html lang="en">
<head>
<meta charset="utf-8">
<title>Varden Therapy – Business Card</title>
<link rel="stylesheet" href="https://fonts.googleapis.com/css2?family=Lora:wght@400;700&display=swap">
<style>
  :root {
    --backdrop: #3a3a3c;
    --card: #1c1c1e;
    --silver: #a9a9ad;
    --brand-green: #2f7a5a;
    --brand-blue: #2c5486;
    --text-light: #e9e9ea;
    --text-muted: #cfcfd2;
  }
  * { margin: 0; padding: 0; box-sizing: border-box; }
  html, body {
    width: 799px; height: 1200px; overflow: hidden;
    background: var(--backdrop);
    font-family: "Lora", Georgia, serif;
  }
  .sheet {
    width: 799px; height: 1200px;
    display: flex; flex-direction: column; align-items: center; justify-content: center;
    gap: 120px;
  }
  .card {
    position: relative;
    width: 620px; height: 354px;
    background: var(--card);
    border-radius: 22px;
    box-shadow: 0 14px 30px rgba(0,0,0,.45);
    overflow: hidden;
  }
  /* front */
  .card-front { display: flex; align-items: center; justify-content: center; }
  .front-wordmark {
    display: flex; align-items: center; gap: 16px;
    color: var(--silver);
    font-weight: 700; font-size: 46px; letter-spacing: 6px;
    text-transform: uppercase;
  }
  .front-wordmark .mark-square { width: 22px; height: 22px; background: var(--silver); }

  /* back */
  .back-band {
    position: absolute; left: 0; right: 0; bottom: 0;
    height: 16px; background: var(--brand-blue);
  }
  .back-content { position: absolute; left: 40px; top: 38px; right: 40px; }
  .back-wordmark {
    display: flex; align-items: center; gap: 12px;
    color: var(--brand-green);
    font-weight: 700; font-size: 34px; letter-spacing: 4px;
    text-transform: uppercase;
  }
  .back-wordmark .mark-square { width: 16px; height: 16px; background: var(--brand-blue); }
  .slogan { margin-top: 8px; color: var(--text-light); font-size: 16px; font-weight: 700; }
  .person-name {
    margin-top: 18px; color: var(--brand-blue);
    font-size: 26px; font-weight: 700; text-transform: uppercase; letter-spacing: 1px;
  }
  .credentials { margin-top: 2px; color: var(--text-muted); font-size: 15px; }
  .social { margin-top: 6px; display: flex; align-items: center; gap: 8px; color: var(--text-muted); font-size: 15px; }
  .social-dot { width: 20px; height: 20px; border-radius: 50%; background: var(--brand-blue); }
  .social-dot.alt { background: var(--brand-green); }
  .contact-list { margin-top: 14px; list-style: none; }
  .contact-list li {
    display: flex; align-items: center; gap: 12px;
    color: var(--text-light); font-size: 16px; line-height: 1.6;
  }
  .contact-icon { width: 14px; height: 14px; flex: none; }
</style>
</head>
<body>
<main class="sheet">

  <section class="card card-front" aria-label="Card front">
    <div class="front-wordmark"><span class="mark-square"></span>Varden Therapy</div>
  </section>

  <section class="card card-back" aria-label="Card back">
    <div class="back-band" aria-hidden="true"></div>
    <div class="back-content">
      <div class="back-wordmark"><span class="mark-square"></span>Varden Therapy</div>
      <p class="slogan">Mobile Physiotherapy - Your Road To Recovery</p>
      <h1 class="person-name">Luke Varden</h1>
      <p class="credentials">BSc(kin), MPT, CAFCI, IMS</p>
      <div class="social">Follow us on: <span class="social-dot"></span><span class="social-dot alt"></span></div>
      <ul class="contact-list">
        <li>
          <svg class="contact-icon" viewBox="0 0 14 14" aria-hidden="true"><path d="M3 1h3l1 3-2 1.5a8 8 0 0 0 3.5 3.5L10 7l3 1v3a2 2 0 0 1-2 2A10 10 0 0 1 1 3a2 2 0 0 1 2-2z" fill="var(--brand-green)"/></svg>
          867-555-0142
        </li>
        <li>
          <svg class="contact-icon" viewBox="0 0 14 14" aria-hidden="true"><rect x="1" y="3" width="12" height="8" fill="none" stroke="var(--brand-green)" stroke-width="1.5"/><path d="M1 3l6 5 6-5" fill="none" stroke="var(--brand-green)" stroke-width="1.5"/></svg>
          VardenTherapy@postnest.ca
        </li>
        <li>
          <svg class="contact-icon" viewBox="0 0 14 14" aria-hidden="true"><circle cx="7" cy="7" r="5.5" fill="none" stroke="var(--brand-green)" stroke-width="1.4"/><path d="M1.5 7h11M7 1.5c-3 3.5-3 7.5 0 11M7 1.5c3 3.5 3 7.5 0 11" fill="none" stroke="var(--brand-green)" stroke-width="1.1"/></svg>
          www.VardenTherapy.ca
        </li>
      </ul>
    </div>
  </section>

</main>
</body>
</html>
```